Business Card Design needed - Something Awesome!

Need a business card designed. Company is "Marlowe Advisory" we do consulting and also have sales automation technology.
I'm going to use thick stock or metal, something really nice... I was thinking about a QR Code on the back that would just upload my contact info to the persons contact, etc -

This is a Strategy Company with a tech feel. I'm open to ideas but really want this to be nice!

I need a template that should include:

Name | Position or Title
D: 415.902.3376
www.marloweadvisory.example

I'm going to attach my contact so you can use that one, I need to get this printed.

Target Market(s)

Small to mid size customers, Entrepreneurs etc.

Industry/Entity Type

Consulting, Tech, Private Equity.

Contact Information for Business Card

Name, Phone, Maybe email, URL

Font styles to use
Sans Serif

Colors

Designer to choose only greyscale colors for use in the design.

Requirements
Must have
• Fresh, Clean, stand out from the crowd - will be on thick stock or metal.
Nice to have
• Clean, simple yet impactful.
Should not have
• Not cartoonish

```html
<!DOCTYPE html>
<html lang="en">
<head>
<meta charset="utf-8">
<title>Marlowe Advisory – Business Card</title>
<link href="https://fonts.googleapis.com/css2?family=Mulish:wght@400;600;800&display=swap" rel="stylesheet">
<style>
  :root {
    --page: #2b2b2b;
    --ink: #000000;
    --paper: #ffffff;
    --text-dark: #111111;
  }
  html, body {
    margin: 0;
    padding: 0;
    width: 1093px;
    height: 1200px;
    overflow: hidden;
    background: var(--page);
    font-family: "Mulish", sans-serif;
  }
  .card {
    position: absolute;
    left: 264px;
    width: 580px;
    height: 360px;
    background: var(--ink);
    overflow: hidden;
  }
  .card--front { top: 226px; }
  .card--back { top: 620px; }

  .wordmark {
    position: absolute;
    margin: 0;
    color: var(--paper);
    font-weight: 600;
    line-height: 1;
    letter-spacing: 0.01em;
  }
  .card--front .wordmark {
    left: 26px;
    top: 48px;
    font-size: 50px;
  }
  .info-band {
    position: absolute;
    left: 0;
    top: 128px;
  }
  .contact {
    position: absolute;
    left: 26px;
    top: 150px;
    color: var(--text-dark);
  }
  .contact__name {
    margin: 0;
    font-size: 21px;
    font-weight: 800;
    line-height: 1;
    letter-spacing: 0.01em;
  }
  .contact__title {
    margin: 2px 0 0;
    font-size: 16px;
    font-weight: 400;
    line-height: 1.1;
  }
  .contact__list {
    list-style: none;
    margin: 22px 0 0;
    padding: 0;
    font-size: 16px;
    line-height: 1;
  }
  .contact__item {
    display: flex;
    align-items: center;
    gap: 7px;
    height: 21px;
  }
  .contact__icon {
    width: 15px;
    height: 15px;
    fill: var(--text-dark);
  }

  .card--back .wordmark {
    left: 0;
    right: 0;
    top: 140px;
    text-align: center;
    font-size: 78px;
  }
  .card__url {
    position: absolute;
    left: 0;
    right: 0;
    top: 298px;
    margin: 0;
    text-align: center;
    color: var(--paper);
    font-size: 15px;
    font-weight: 600;
  }
</style>
</head>
<body>
  <section class="card card--front" aria-label="Business card front">
    <h1 class="wordmark">MARLOWE</h1>
    <svg class="info-band" width="580" height="159" viewBox="0 0 580 159" aria-hidden="true">
      <polygon points="0,0 422,0 296,159 0,159" fill="var(--paper)"/>
    </svg>
    <div class="contact">
      <p class="contact__name">ELLIOT MARSH</p>
      <p class="contact__title">Managing Director</p>
      <ul class="contact__list">
        <li class="contact__item">
          <svg class="contact__icon" viewBox="0 0 24 24" aria-hidden="true">
            <path d="M6.6 10.8a15.1 15.1 0 0 0 6.6 6.6l2.2-2.2a1 1 0 0 1 1-.25 11.4 11.4 0 0 0 3.6.57 1 1 0 0 1 1 1V20a1 1 0 0 1-1 1A17 17 0 0 1 3 4a1 1 0 0 1 1-1h3.5a1 1 0 0 1 1 1c0 1.25.2 2.45.57 3.6a1 1 0 0 1-.25 1z"/>
          </svg>
          <span>415.902.3376</span>
        </li>
        <li class="contact__item">
          <svg class="contact__icon" viewBox="0 0 24 24" aria-hidden="true">
            <path d="M2 5h20v14H2z M3.5 6.5l8.5 6.5 8.5-6.5" fill="var(--text-dark)"/>
            <path d="M3.5 6.5l8.5 6.5 8.5-6.5" fill="none" stroke="var(--paper)" stroke-width="1.4"/>
          </svg>
          <span>info@marloweadvisory.example</span>
        </li>
      </ul>
    </div>
  </section>

  <section class="card card--back" aria-label="Business card back">
    <h2 class="wordmark">MARLOWE</h2>
    <p class="card__url">www.marloweadvisory.example</p>
  </section>
</body>
</html>
```